Events and Brand activation brochure

We are looking for a new Brochure. This Brochure's main focus is pictures (minimal text). I have attached the template including all the pictures and page titles we would like. We are working on the text at the moment however, we need a better idea of where to place the text. The pictures that are placed individually on a seperate page are to stay that way with no text. The pages with more than one picture on them, they can be created into a collage of some sort? We dont need much text space as it will mainly be bullet points. We would like a cool looking map on the back showcasing all of our locations as shown in the template.
Please follow our Logo design throughout the pages which is also uploaded.
The Brochure should be more of a booklet (LANDSCAPE- 24cmX25cm)

Industry/Entity Type

Events

Colors
3276b5
85acd3
0555a3
85cae6

Requirements
Must have
• Landscape
• Booklet
Nice to have
• Include one of the Brimmel Spire pictures faded out as background for ''about us page''??

```html
<!DOCTYPE html>
<html lang="en">
<head>
<meta charset="utf-8">
<title>Avelo Events Brochure – Covers</title>
<link href="https://fonts.googleapis.com/css2?family=Open+Sans:ital,wght@0,400;0,600;0,700;1,400;1,700&display=swap" rel="stylesheet">
<style>
  :root{
    --stage:#e9eaee;
    --paper:#ffffff;
    --navy:#1c3b6f;
    --brand-blue:#3276b5;
    --accent:#f0a030;
    --ink:#3a4150;
    --sepia-light:#c9a677;
    --sepia-mid:#8a6438;
    --sepia-dark:#2a1c0e;
  }
  *{box-sizing:border-box;margin:0;padding:0}
  html,body{width:1200px;height:730px;overflow:hidden;background:var(--stage);font-family:"Open Sans",Arial,sans-serif;color:var(--ink)}
  .spread{position:absolute;left:40px;top:85px;width:1120px;height:560px;display:flex;box-shadow:0 10px 30px rgba(0,0,0,.18)}
  .page{position:relative;width:560px;height:560px;overflow:hidden}

  /* Back cover */
  .back-cover{background:var(--paper)}
  .brand{position:absolute;display:flex;align-items:center;gap:8px;color:var(--navy);font-weight:600;letter-spacing:.3em}
  .back-cover .brand{left:44px;top:44px;font-size:20px}
  .brand-dot{width:12px;height:12px;border-radius:50%;background:var(--brand-blue)}
  .office-list{position:absolute;left:44px;top:150px;list-style:none;font-size:10.5px;line-height:1.45;color:var(--ink)}
  .office-list li{display:flex;gap:8px;margin-bottom:18px}
  .office-list svg{flex:none;margin-top:1px}
  .locations-map{position:absolute;left:190px;top:28px;width:350px;height:300px;border-radius:6px;
    background:linear-gradient(135deg,#8fb6e0 0%,#f3b04a 35%,#e9865a 55%,#7fc98a 75%,#9a8fd9 100%);opacity:.85}
  .contact-band{position:absolute;left:0;bottom:0;width:560px;height:220px}
  .contact-content{position:absolute;left:0;bottom:0;width:560px;height:180px;color:#fff}
  .contact-title{position:absolute;left:44px;top:30px;font-size:20px;font-weight:700;font-style:italic;letter-spacing:.02em}
  .contact-title span{font-weight:400;opacity:.75}
  .contact-rule{position:absolute;left:44px;top:60px;width:80px;height:2px;background:var(--accent)}
  .contact-line{position:absolute;left:44px;display:flex;align-items:center;gap:8px;font-size:12px}
  .contact-line.phone{top:76px;font-weight:700}
  .contact-line.web{top:100px}
  .contact-line.web strong{font-weight:700}
  .hq-address{position:absolute;left:250px;top:76px;display:flex;gap:8px;font-size:10.5px;line-height:1.45}
  .contact-line.mail{left:auto;right:44px;top:140px;font-style:italic;font-size:11px}

  /* Front cover */
  .front-cover{background:var(--sepia-dark)}
  .cover-photo{position:absolute;inset:0;
    background:radial-gradient(ellipse at 75% 45%,#f0dcb4 0%,var(--sepia-light) 25%,var(--sepia-mid) 60%,var(--sepia-dark) 100%)}
  .cover-frame{position:absolute;left:22px;top:22px;right:22px;bottom:22px;border:3px solid #fff}
  .cover-badge{position:absolute;right:0;top:300px;width:210px;height:130px;background:#fff;border:1px solid var(--navy);
    display:flex;flex-direction:column;align-items:center;justify-content:center;gap:14px}
  .cover-badge .brand{position:static;font-size:22px}
  .cover-url{font-size:14px;color:var(--navy)}
  .cover-url strong{font-weight:700}
</style>
</head>
<body>
<main class="spread">
  <section class="page back-cover">
    <div class="brand"><span class="brand-dot"></span>AVELO</div>

    <ul class="office-list">
      <li>
        <svg width="10" height="13" viewBox="0 0 10 13"><path d="M5 0a5 5 0 0 0-5 5c0 4 5 8 5 8s5-4 5-8a5 5 0 0 0-5-5z" fill="var(--accent)"/><circle cx="5" cy="5" r="2" fill="#fff"/></svg>
        <span>Calle Marina Alta Núm.7<br>Polígono Les Salines<br>Viladecans Sud 08840<br>Barcelona SPAIN</span>
      </li>
      <li>
        <svg width="10" height="13" viewBox="0 0 10 13"><path d="M5 0a5 5 0 0 0-5 5c0 4 5 8 5 8s5-4 5-8a5 5 0 0 0-5-5z" fill="var(--accent)"/><circle cx="5" cy="5" r="2" fill="#fff"/></svg>
        <span>Lindenhofer Str. 42,<br>10437 Berlin,<br>GERMANY</span>
      </li>
    </ul>

    <div class="locations-map" role="img" aria-label="Colourful map of Europe with each country in a different flat colour, showing office locations"></div>

    <svg class="contact-band" viewBox="0 0 560 220" preserveAspectRatio="none" aria-hidden="true">
      <path d="M0 40 Q300 70 560 0 L560 220 L0 220 Z" fill="var(--navy)"/>
    </svg>
    <div class="contact-content">
      <div class="contact-title">CONTACT <span>US</span></div>
      <div class="contact-rule"></div>
      <div class="contact-line phone">
        <svg width="12" height="12" viewBox="0 0 12 12"><circle cx="6" cy="6" r="5.3" fill="none" stroke="var(--accent)" stroke-width="1.2"/><path d="M4 3.5l1 1-.6.8a4 4 0 0 0 2.3 2.3l.8-.6 1 1-.8 1A5 5 0 0 1 3 4.3z" fill="var(--accent)"/></svg>
        +44 (0)20 7946 0182
      </div>
      <div class="contact-line web">
        <svg width="12" height="12" viewBox="0 0 12 12"><circle cx="6" cy="6" r="5.3" fill="none" stroke="var(--accent)" stroke-width="1.2"/><path d="M0.7 6h10.6M6 0.7c-3 3-3 7.6 0 10.6M6 0.7c3 3 3 7.6 0 10.6" fill="none" stroke="var(--accent)" stroke-width="1"/></svg>
        <span>www.<strong>avelo</strong>-events.com</span>
      </div>
      <div class="hq-address">
        <svg width="10" height="13" viewBox="0 0 10 13"><path d="M5 0a5 5 0 0 0-5 5c0 4 5 8 5 8s5-4 5-8a5 5 0 0 0-5-5z" fill="var(--accent)"/><circle cx="5" cy="5" r="2" fill="var(--navy)"/></svg>
        <span>Unit 4,<br>Harrowgate Trade Park,<br>Harrowgate Lane,<br>London,<br>E15 9QX</span>
      </div>
      <div class="contact-line mail">
        <svg width="13" height="9" viewBox="0 0 13 9"><rect x=".5" y=".5" width="12" height="8" fill="none" stroke="var(--accent)"/><path d="M.5 .5l6 4.5 6-4.5" fill="none" stroke="var(--accent)"/></svg>
        hello@avelo-events.com
      </div>
    </div>
  </section>

  <section class="page front-cover">
    <div class="cover-photo" role="img" aria-label="Sepia photograph of the Brimmel Spire observation wheel against a cloudy sky above riverside buildings"></div>
    <div class="cover-frame"></div>
    <div class="cover-badge">
      <div class="brand"><span class="brand-dot"></span>AVELO</div>
      <div class="cover-url">www.<strong>avelo</strong>-events.com</div>
    </div>
  </section>
</main>
</body>
</html>
```